Online interactive tutorial for year 2 to year 12 students in Australia

Website design for a new online tutorial for year 2 to year 12 students in Australia.

- The tutorial will be conducted via live webcam and within a dedicated interactive space
- The tutorial will be provided by high scoring undergraduates studying in top Australian universities.
- The tutors will be going through interviews & assessments & only top students are allowed to apply.
- Parents will do search and select tutor and have short 15 mins video interaction with potential tutors before booking them for their children for tutoring.
- hourly cost of booking (no monthly subscription or no hour limits)
- Tutors will have their own profile

Please see the attached for detailed page functionality.

The look and feel of the design must consider the following:
- must be educational but not dull and should stand out
- must appeal to younger generation - tutees (8-18 years), tutors (19-25), parents (30-50).
- Ideas for Logos (brivora.com.au but not confirmed)

Target Market(s)

tutees (8-18 years), tutors (19-25 years), parents (30-50 years).

Industry/Entity Type

Education

Coding

Coded - Design and coding required

Number of Pages Required

5+ page

Font styles to use
Serif

Requirements
Must have
• The look and feel of the design must consider the following:
• - must be educational but not dull and should stand out
• - must appeal to younger generation - tutees (8-18 years), tutors (19-25), parents (30-50).
Should not have
• Dullness

```html
<!DOCTYPE html>
<html lang="en">
<head>
<meta charset="utf-8">
<title>Brivora – Tutor Registration</title>
<link href="https://fonts.googleapis.com/css2?family=Open+Sans:wght@400;600;700&family=Roboto:wght@400;500&family=Roboto+Condensed:wght@700&display=swap" rel="stylesheet">
<style>
:root{
  --blue:#2a7bc0;
  --blue-line:#2a9ee0;
  --orange:#ff6a0c;
  --cyan:#1aa3d9;
  --ink:#333;
  --muted:#555;
  --field-bg:#f9f9f9;
  --field-line:#dcdcdc;
  --footer:#3a3a3a;
  --white:#fff;
}
*{box-sizing:border-box;margin:0;padding:0}
html,body{width:957px;height:1200px;overflow:hidden;background:var(--white);font-family:"Open Sans",sans-serif;color:var(--ink)}
.page{position:relative;width:957px;height:1200px}
.abs{position:absolute}
.brand{left:78px;top:22px;display:flex;align-items:center;gap:10px;font-size:30px;font-weight:700;color:#4a4a4a}
.brand-dot{width:30px;height:30px;border-radius:50%;background:var(--blue)}
.search{left:289px;top:30px;width:287px;height:27px;border:1px solid #ccc;border-radius:2px;display:flex;font-size:10px;color:#444}
.search span{flex:1;padding:7px 11px}
.search .caret{flex:none;width:0;height:0;border:3px solid transparent;border-top:4px solid #777;margin:12px 10px 0 0}
.search button{width:30px;border:none;border-left:1px solid #ccc;background:#e9e9e9;display:flex;align-items:center;justify-content:center}
.role{top:31px;height:26px;border:2px solid var(--blue);border-radius:2px;color:var(--blue);font-family:Roboto,sans-serif;font-size:11px;display:flex;align-items:center;justify-content:center;gap:5px}
.login{left:823px;top:30px;width:55px;height:27px;background:var(--blue);color:var(--white);font-family:Roboto,sans-serif;font-size:11px;display:flex;align-items:center;justify-content:center;border-radius:2px}
.nav{left:0;top:92px;width:957px;height:39px;background:var(--blue);display:flex;padding-left:78px}
.nav a{color:var(--white);text-decoration:none;font-family:Roboto,sans-serif;font-size:11px;display:flex;align-items:center;padding:0 19px;border-right:1px solid #2469a6}
.nav a:last-child{border-right:none}
.hero{left:0;top:131px;width:957px;height:261px;background:linear-gradient(100deg,#6f7c86 0%,#4a5058 40%,#3e3a3a 70%,#5a5f66 100%)}
.hero-cut{left:0;top:131px}
.hero-title{left:0;top:250px;width:957px;text-align:center;color:var(--white);font-family:"Roboto Condensed",sans-serif;font-weight:700;font-size:33px;letter-spacing:.3px}
.field{height:30px;background:var(--field-bg);border:1px solid var(--field-line);font-size:9px;color:var(--ink);padding:0 12px;display:flex;align-items:center}
.field em{font-style:normal;color:#999;margin-left:4px}
.upload{width:66px;height:30px;background:#e9e9e9;border:1px solid #ccc;border-radius:3px;font-size:11px;display:flex;align-items:center;justify-content:center;color:#444}
.l{left:174px;width:294px}
.r{left:489px;width:293px}
.short{width:221px}
.exp{left:174px;top:638px;font-size:9px}
.exp .opts{display:flex;align-items:center;gap:5px;margin-top:8px;font-size:8.5px}
.box{width:8px;height:8px;border:1px solid #bbb;display:inline-block}
.notes{left:174px;top:758px;width:608px;height:127px;align-items:flex-start;padding-top:10px}
.btn{top:903px;height:26px;color:var(--white);font-family:Roboto,sans-serif;font-size:13px;display:flex;align-items:center;justify-content:center;border-radius:2px}
.footer{left:0;top:970px;width:957px;height:230px;background:var(--footer);color:var(--white)}
.footer h3{position:absolute;top:28px;font-family:Roboto,sans-serif;font-weight:400;font-size:14px}
.contact p{font-size:10.5px;line-height:16px;letter-spacing:.2px}
.links{list-style:none;font-size:10.5px}
.links li{height:17px;display:flex;align-items:center;gap:9px}
.links li:before{content:"";border:3px solid transparent;border-left:4px solid var(--white)}
.news p{font-size:8.5px;line-height:15px}
.news .in{margin-top:14px;width:234px;height:33px;background:var(--white);color:#555;font-size:9px;padding:0 11px;display:flex;align-items:center}
.news .sub{margin-top:7px;width:81px;height:33px;background:var(--cyan);font-family:Roboto,sans-serif;font-size:11px;display:flex;align-items:center;justify-content:center}
.social li{list-style:none;display:flex;align-items:center;gap:8px;height:29px;font-size:11.5px}
.social .ring{width:20px;height:20px;border:1px solid #ddd;border-radius:50%}
</style>
</head>
<body>
<div class="page">
  <header>
    <div class="abs brand"><span class="brand-dot"></span>Brivora</div>
    <div class="abs search"><span>Search</span><i class="caret"></i><button aria-label="Search"><svg width="10" height="10" viewBox="0 0 10 10"><circle cx="4" cy="4" r="3" fill="none" stroke="#555" stroke-width="1.4"/><line x1="6.3" y1="6.3" x2="9" y2="9" stroke="#555" stroke-width="1.5"/></svg></button></div>
    <div class="abs role" style="left:594px;width:62px"><svg width="9" height="10"><circle cx="4.5" cy="3" r="2.7" fill="#2a7bc0"/><rect x="0.5" y="6" width="8" height="4" rx="2" fill="#2a7bc0"/></svg>Tutor</div>
    <div class="abs role" style="left:664px;width:66px"><svg width="10" height="11"><circle cx="3" cy="2" r="1.8" fill="#2a7bc0"/><circle cx="7.5" cy="2" r="1.8" fill="#2a7bc0"/><rect x="1" y="4.5" width="4" height="6.5" fill="#2a7bc0"/><rect x="5.5" y="4.5" width="4" height="6.5" fill="#2a7bc0"/></svg>Parent</div>
    <div class="abs role" style="left:740px;width:74px"><svg width="11" height="10"><polygon points="5.5,0 11,2.5 5.5,5 0,2.5" fill="#2a7bc0"/><rect x="3" y="4" width="5" height="6" fill="#2a7bc0"/></svg>Tutees</div>
    <div class="abs login">LOGIN</div>
  </header>
  <nav class="abs nav">
    <a>HOME</a><a>TUTOR PROFILES</a><a>HOW IT WORKS</a><a>TESTIMONIALS</a><a>PRICES</a><a>CONTACT US</a>
  </nav>
  <section>
    <div class="abs hero" role="img" aria-label="Photo of hands typing on a laptop keyboard"></div>
    <svg class="abs hero-cut" width="957" height="262" viewBox="0 0 957 262">
      <polygon points="0,205 479,261 957,205 957,262 0,262" fill="#fff"/>
      <polyline points="0,203 479,259 957,203" fill="none" stroke="#2a9ee0" stroke-width="4"/>
    </svg>
    <h1 class="abs hero-title">TUTOR REGISTRATION</h1>
  </section>
  <form>
    <div class="abs field l short" style="top:430px">Profile Picture</div>
    <div class="abs upload" style="left:402px;top:430px">Upload</div>
    <div class="abs field r" style="top:430px">First Name / Last Name</div>
    <div class="abs field l" style="top:471px">Institution</div>
    <div class="abs field r" style="top:471px">Email</div>
    <div class="abs field l" style="top:512px">Phone</div>
    <div class="abs field r" style="top:512px">Nationality</div>
    <div class="abs field l" style="top:553px">Work Permit question</div>
    <div class="abs field r" style="top:553px">Profile</div>
    <div class="abs field l" style="top:594px">Qualification/Grades</div>
    <div class="abs field r" style="top:594px">Graduation Month &amp; Year</div>
    <div class="abs exp">Previous tutoring experience
      <div class="opts"><span class="box"></span>Yes <span style="font-size:7.5px">Or</span> <span class="box" style="margin-left:3px"></span>No</div>
    </div>
    <div class="abs field r" style="top:635px">Tutorial subjects</div>
    <div class="abs field l" style="top:676px"></div>
    <div class="abs field r" style="top:676px">Username<em>(the email address)</em></div>
    <div class="abs field l short" style="top:717px">Upload: CV, Education Transcripts</div>
    <div class="abs upload" style="left:402px;top:717px">Upload</div>
    <div class="abs field r" style="top:717px">Create a password</div>
    <div class="abs field notes">Webcam Interview &amp; Assessment</div>
    <div class="abs btn" style="left:395px;width:79px;background:var(--orange)">Submit</div>
    <div class="abs btn" style="left:484px;width:78px;background:var(--blue)">Register</div>
  </form>
  <footer class="abs footer">
    <h3 style="left:78px">CONTACT US</h3>
    <div class="abs contact" style="left:78px;top:58px">
      <p>Level 3, 22 Harbour Lane, Brisbane<br>QLD 4000, Australia</p>
      <div style="display:flex;gap:14px;margin-top:10px"><svg width="16" height="16" viewBox="0 0 16 16"><path d="M3 2l3 3-1.5 2c1 2 2.5 3.5 4.5 4.5L11 10l3 3-2 2C7 14 2 9 1 4z" fill="none" stroke="#ddd" stroke-width="1"/></svg><p>Phone : +61 7 3555 0142<br>Fax : +61 7 3555 0143</p></div>
      <div style="display:flex;gap:14px;margin-top:10px;align-items:center"><svg width="16" height="12" viewBox="0 0 16 12"><rect x="0.5" y="0.5" width="15" height="11" fill="none" stroke="#ddd"/><polyline points="0.5,0.5 8,7 15.5,0.5" fill="none" stroke="#ddd"/></svg><p>Email: info@brivora.com.au</p></div>
    </div>
    <h3 style="left:338px">USEFUL LINKS</h3>
    <ul class="abs links" style="left:338px;top:63px">
      <li>Home</li><li>About Us</li><li>Services</li><li>Tutor Profile</li><li>How It Works</li><li>Scheduler</li><li>Testimonials</li><li>Contact Us</li>
    </ul>
    <h3 style="left:497px">JOIN OUR NEWSLETTER</h3>
    <div class="abs news" style="left:497px;top:58px">
      <p>Sed ut perspiciatis unde omnis iste natus error sit volup-<br>tatem accusantium doloremque laudantium,</p>
      <div class="in">Enter Name</div>
      <div class="sub">SUBSCRIBE</div>
    </div>
    <h3 style="left:802px">SOCIAL</h3>
    <ul class="abs social" style="left:802px;top:59px">
      <li><span class="ring"></span>Huddle</li>
      <li><span class="ring"></span>Chirper</li>
      <li><span class="ring"></span>Circles</li>
      <li><span class="ring"></span>Clipcast</li>
    </ul>
  </footer>
</div>
</body>
</html>
```